American cannabis tech company business card design

Pavrel.com is seeking a modern, professional, and brand-aligned business card that represents our company and its core values: Mission, Story, Values, and Impact. As an innovative cannabis company, we want a business card that is not only visually appealing but also serves as a representation of who we are and what we stand for.

Project Scope: Design a double-sided business card that integrates our brand identity and core values. Incorporate our key brand elements, ensuring a sleek and contemporary aesthetic. Visually reflect our core values (Mission, Story, Values, Impact) in a way that is engaging yet professional.

Target Market(s)

Vendors, third parties,

Contact Information for Business Card

Contact details (name, title, email, phone, website, etc.)

Font styles to use
Other font styles liked:
• Caslon, Centra

Colors

Designer to choose colors to be used in the design.

Requirements
Must have
• Pavrel.com logo and branding A creative yet clean way to integrate our core values (Mission, Story, Values, Impact) Modern typography and a well-structured layout
Nice to have
• forest green, grey, white, black
Should not have
• references to marijuana, leafs, plants, or related product

```html
<!DOCTYPE html>
<html lang="en">
<head>
<meta charset="utf-8">
<title>Pavrel.com Business Card</title>
<link href="https://fonts.googleapis.com/css2?family=Poppins:wght@400;600;700&display=swap" rel="stylesheet">
<style>
  :root {
    --forest: #1b3a1f;
    --forest-deep: #16311a;
    --paper: #ffffff;
    --backdrop: #222222;
    --ink-light: #ffffff;
  }
  * { margin: 0; padding: 0; box-sizing: border-box; }
  html, body {
    width: 1200px; height: 1015px; overflow: hidden;
    background: var(--backdrop);
    font-family: "Poppins", sans-serif;
  }
  .stage { position: relative; width: 1200px; height: 1015px; }
  .card {
    position: absolute; left: 290px; width: 620px; height: 354px;
    background: var(--paper); overflow: hidden;
    box-shadow: 0 10px 30px rgba(0,0,0,.5);
  }
  .card--front { top: 90px; }
  .card--back { top: 504px; }

  .wordmark {
    position: absolute; font-weight: 700; color: var(--forest);
    letter-spacing: 1px; line-height: 1;
  }
  .card--front .wordmark {
    left: 0; right: 0; top: 145px; text-align: center; font-size: 58px;
  }
  .card--back .wordmark { left: 34px; top: 168px; font-size: 50px; }

  .wave { position: absolute; inset: 0; width: 100%; height: 100%; }

  .person {
    position: absolute; right: 34px; top: 28px; text-align: right; color: var(--forest);
  }
  .person__name { font-weight: 700; font-size: 18px; letter-spacing: .5px; line-height: 1.15; }
  .person__title { font-size: 13px; line-height: 1.2; }

  .contact {
    position: absolute; right: 30px; top: 172px; list-style: none;
    color: var(--ink-light); text-align: right; font-size: 14.5px; line-height: 1.4;
  }
  .contact li { display: flex; justify-content: flex-end; align-items: center; gap: 8px; }
  .contact li.contact__address { align-items: flex-start; margin-top: 8px; }
  .contact .icon { width: 15px; height: 15px; flex: none; }
</style>
</head>
<body>
<main class="stage">
  <section class="card card--front" aria-label="Card front">
    <div class="wordmark">PAVREL</div>
  </section>

  <section class="card card--back" aria-label="Card back">
    <svg class="wave" viewBox="0 0 620 354" preserveAspectRatio="none" aria-hidden="true">
      <path d="M0,238 C120,300 250,275 345,200 C430,132 510,102 620,94"
            fill="none" stroke="var(--forest)" stroke-width="8"/>
      <path d="M0,262 C130,320 260,298 355,222 C440,152 520,124 620,116 L620,354 L0,354 Z"
            fill="var(--forest-deep)"/>
    </svg>

    <div class="wordmark">PAVREL</div>

    <div class="person">
      <div class="person__name">DANIEL HARPER</div>
      <div class="person__title">Managing Director</div>
    </div>

    <ul class="contact">
      <li>044-555 218 604
        <svg class="icon" viewBox="0 0 16 16"><circle cx="8" cy="8" r="7.5" fill="#fff"/><path d="M5 4.5l1.6-.4 1 2-1 .8a5 5 0 0 0 2.5 2.5l.8-1 2 1-.4 1.6C9 11.5 4.5 7 5 4.5z" fill="var(--forest)"/></svg>
      </li>
      <li>info@pavrel.com
        <svg class="icon" viewBox="0 0 16 16"><rect x="1" y="3.5" width="14" height="9" fill="#fff"/><path d="M1 3.5l7 5 7-5" fill="none" stroke="var(--forest)" stroke-width="1.2"/></svg>
      </li>
      <li>www.pavrel.com
        <svg class="icon" viewBox="0 0 16 16"><circle cx="8" cy="8" r="7.5" fill="#fff"/><g fill="none" stroke="var(--forest)" stroke-width="1"><circle cx="8" cy="8" r="5.5"/><ellipse cx="8" cy="8" rx="2.4" ry="5.5"/><path d="M2.5 8h11M3.5 5h9M3.5 11h9"/></g></svg>
      </li>
      <li class="contact__address"><span>218 Alder Street<br>Portland, OR 97205</span>
        <svg class="icon" viewBox="0 0 16 16"><path d="M8 1a5 5 0 0 1 5 5c0 3.5-5 9-5 9S3 9.5 3 6a5 5 0 0 1 5-5z" fill="#fff"/><circle cx="8" cy="6" r="1.8" fill="var(--forest)"/></svg>
      </li>
    </ul>
  </section>
</main>
</body>
</html>
```